Pine Hollow Haven Home Inc. Website Update

We have a couple of broken links such as the "contact us" and would like to add board members and a calendar of events. We are open to a new design.

```html
<!DOCTYPE html>
<html lang="en">
<head>
<meta charset="utf-8">
<title>Pine Hollow Haven Home Inc.</title>
<link href="https://fonts.googleapis.com/css2?family=Open+Sans:wght@400;600;700&family=Roboto:wght@400;500;700&display=swap" rel="stylesheet">
<style>
:root{
  --crimson:#9c1a3e;
  --crimson-dark:#7d1230;
  --rose:#d65a7c;
  --navy:#1c2a3f;
  --navy-deep:#131d2c;
  --blue:#1f74c4;
  --ink:#222;
  --muted:#666;
  --light:#f3f3f3;
  --white:#fff;
  --star:#f2b01e;
  --head:'Roboto',sans-serif;
  --body:'Open Sans',sans-serif;
}
*{box-sizing:border-box;margin:0;padding:0}
html,body{width:1200px;height:4467px;overflow:hidden}
body{position:relative;background:var(--white);font-family:var(--body);color:var(--ink)}
.abs{position:absolute}
.section-title{position:absolute;left:0;width:1200px;text-align:center;font-family:var(--head);font-size:36px;font-weight:400;letter-spacing:.5px}

/* top bar */
.topbar{left:0;top:0;width:1200px;height:36px;background:var(--navy)}
.topbar .contact{left:90px;top:9px;color:#dde;font-size:12px;display:flex;gap:26px}
.topbar .contact span::before{content:"";display:inline-block;width:10px;height:9px;background:#dde;margin-right:6px;border-radius:1px}
.donate{left:908px;top:0;width:98px;height:36px;background:#0f1a2a;color:#fff;font-size:13px;font-weight:600;text-align:center;line-height:36px}
.social-top{left:1018px;top:11px;display:flex;gap:6px}
.social-top i,.social-foot i{display:block;width:15px;height:15px;background:#fff;border-radius:2px}

/* nav */
.navbar{left:0;top:36px;width:1200px;height:101px;background:#fff;box-shadow:0 2px 6px rgba(0,0,0,.08);z-index:3}
.brand{left:88px;top:12px;display:flex;align-items:center;gap:10px}
.brand .mark{width:22px;height:22px;border-radius:50%;background:var(--crimson)}
.brand .name{font-family:var(--head);font-weight:700;font-size:14px;color:var(--crimson);width:130px;line-height:1.2}
.nav{font-family:var(--head);font-size:14px;color:#333}
.nav a{color:inherit;text-decoration:none;position:absolute;white-space:nowrap}
.nav a.active{color:var(--crimson)}

/* hero */
.hero{left:0;top:137px;width:1200px;height:593px;background:linear-gradient(100deg,#6c8a5e 0%,#a9b48c 35%,#d9c7a6 55%,#8f8f8a 80%,#c3c3c3 100%)}
.hero-title{left:75px;top:310px;font-family:var(--head);font-weight:700;font-size:92px;color:#fff;line-height:1;text-shadow:0 2px 8px rgba(0,0,0,.25)}
.hero-sub{left:60px;top:430px;font-family:var(--head);font-weight:700;font-size:56px;color:var(--blue);letter-spacing:.5px}
.watch{left:75px;top:526px;display:flex;align-items:center;gap:14px;color:#fff;font-family:var(--head);font-size:16px;font-weight:500}
.watch i{display:block;width:30px;height:30px;border-radius:50%;background:var(--rose);position:relative}
.watch i::after{content:"";position:absolute;left:12px;top:9px;border-left:9px solid #fff;border-top:6px solid transparent;border-bottom:6px solid transparent}
.hero-dots{left:1152px;top:330px;display:flex;flex-direction:column;gap:12px}
.hero-dots i{display:block;width:7px;height:7px;border-radius:50%;background:rgba(255,255,255,.6)}
.hero-dots i.on{background:#fff}

/* about */
.about-bg{left:700px;top:730px;width:500px;height:752px;background:linear-gradient(90deg,#fff 0%,#eef0f2 40%,#dfe2e6 100%);opacity:.9}
.about-lead{left:0;top:870px;width:1200px;text-align:center;font-size:14px;color:#444}
.feature{position:absolute;font-family:var(--head);font-size:19px;line-height:1.35;color:#333}
.feature.left{text-align:right;width:260px}
.feat-icon{position:absolute;width:66px;height:66px;border-radius:50%;background:#fff;box-shadow:0 3px 12px rgba(0,0,0,.15);display:flex;align-items:center;justify-content:center}
.center-photo{left:468px;top:970px;width:292px;height:292px;border-radius:50%;background:#fff;box-shadow:0 4px 20px rgba(0,0,0,.12)}
.center-photo-fill{left:488px;top:990px;width:252px;height:400px;border-radius:126px 126px 40px 40px;background:linear-gradient(180deg,#c79a86 0%,#8e8f95 55%,#5a5d69 100%)}

/* services */
.services-band{left:0;top:1482px;width:1200px;height:411px;background:linear-gradient(90deg,var(--crimson-dark),var(--crimson) 50%,var(--crimson-dark))}
.services-band .section-title{top:96px;color:#fff}
.card{position:absolute;width:298px;height:354px;background:#fff;box-shadow:0 6px 18px rgba(0,0,0,.18)}
.card .photo{height:194px;position:relative}
.card .play{position:absolute;left:129px;top:77px;width:40px;height:40px;border-radius:50%;background:rgba(255,255,255,.85)}
.card .play::after{content:"";position:absolute;left:16px;top:12px;border-left:12px solid var(--ink);border-top:8px solid transparent;border-bottom:8px solid transparent}
.card h3{font-family:var(--head);font-weight:500;font-size:20px;text-align:center;margin-top:30px}
.card p{font-size:12px;color:#777;text-align:center;padding:0 30px;margin-top:8px;line-height:1.4;height:34px;overflow:hidden}
.card .more{display:block;text-align:center;font-size:12px;color:#444;margin-top:14px}
.card.highlight{background:var(--rose);color:#fff}
.card.highlight p,.card.highlight .more{color:#fde}
.dots{left:578px;top:2105px;display:flex;gap:8px}
.dots i{display:block;width:9px;height:9px;border-radius:50%;background:#222}
.dots i.on{background:var(--blue)}

/* testimonials */
.testi{position:absolute;width:452px;height:230px;background:#fff;box-shadow:0 4px 16px rgba(0,0,0,.15)}
.testi .avatar{position:absolute;left:-32px;top:50px;width:116px;height:116px;border-radius:50%;background:linear-gradient(160deg,#c99b82,#6f5a52);border:4px solid #fff;box-shadow:0 2px 8px rgba(0,0,0,.2)}
.testi .quote{position:absolute;right:34px;top:22px;font-family:Georgia,serif;font-size:80px;line-height:1;color:var(--blue);font-weight:700}
.testi p{position:absolute;left:112px;top:70px;width:310px;font-size:15px;line-height:1.6;color:#444}
.testi .stars{position:absolute;left:112px;top:165px;color:var(--star);font-size:14px;letter-spacing:1px}
.testi .who{position:absolute;right:50px;top:168px;color:var(--blue);font-size:15px}

/* board */
.board-band{left:0;top:2709px;width:1200px;height:611px;background:linear-gradient(180deg,var(--navy) 0%,var(--navy-deep) 100%)}
.board-band .section-title{top:92px;color:#fff}
.member{position:absolute;top:2950px;width:312px;height:277px;background:#fff;text-align:center}
.member .avatar{position:absolute;left:86px;top:-72px;width:140px;height:140px;border-radius:50%;border:5px solid #fff;background:linear-gradient(160deg,#d3ab95,#7b6a63)}
.member h4{margin-top:96px;font-family:var(--head);font-weight:500;font-size:20px}
.member .role{color:var(--crimson);font-size:13px;margin-top:4px}
.member p{font-size:13px;line-height:1.6;color:#555;padding:0 30px;margin-top:14px}
.arrow-btn{position:absolute;top:3082px;width:46px;height:46px;border-radius:50%;background:rgba(255,255,255,.3);display:flex;align-items:center;justify-content:center}

/* events */
.calendar{left:90px;top:3528px;width:324px;height:417px;background:#fff;box-shadow:0 4px 16px rgba(0,0,0,.15)}
.cal-head{position:absolute;left:0;top:38px;width:324px;text-align:center;font-family:var(--head);font-size:20px}
.cal-head .mo{display:inline-block;width:160px}
.cal-head b{color:var(--crimson);font-size:26px;font-weight:400;position:absolute;top:-6px}
.cal-grid{position:absolute;left:32px;top:88px;border-collapse:collapse}
.cal-grid td{width:37px;height:38px;text-align:center;font-size:17px;color:#333}
.cal-grid th{height:38px;font-size:15px;font-weight:600;color:#333;border-top:1px solid #ddd}
.cal-grid .dim{color:#aaa}
.cal-grid .today span{display:inline-block;width:30px;height:30px;line-height:30px;border-radius:50%;background:var(--crimson);color:#fff}
.cal-add{position:absolute;left:22px;top:372px;width:24px;height:24px;border-radius:50%;border:2px solid var(--crimson);color:var(--crimson);text-align:center;line-height:19px;font-size:18px}
.event{position:absolute;top:3528px;width:322px;height:417px;background:#fff;box-shadow:0 4px 16px rgba(0,0,0,.15)}
.event .photo{height:214px}
.event h4{font-family:var(--head);font-weight:500;font-size:19px;margin:30px 0 0 26px}
.event p{font-size:13px;color:#888;line-height:1.5;margin:10px 26px 0;height:40px;overflow:hidden}
.event .meta{position:absolute;left:26px;bottom:30px;display:flex;align-items:center;gap:8px;font-size:12px;color:#777}
.event .meta .stars{color:var(--star);font-size:14px}
.event .see{position:absolute;right:34px;bottom:24px;background:var(--crimson);color:#fff;font-size:13px;border-radius:14px;padding:5px 18px}
.view-more{left:1007px;top:3966px;color:var(--crimson);font-size:15px}

/* footer */
.footer{left:0;top:4040px;width:1200px;height:427px}
.badge{left:100px;top:4148px;width:150px;height:150px;border-radius:50%;background:#c9a24a}
.foot-col{position:absolute;top:4152px;color:#fff;font-size:13px}
.foot-col h5{font-family:var(--head);font-weight:500;font-size:14px;letter-spacing:.5px;margin-bottom:20px}
.foot-col li{list-style:none;font-size:12px;line-height:22px;color:#ddd}
.foot-col li::before{content:"» ";}
.foot-contact div{display:flex;align-items:flex-start;gap:12px;margin-bottom:16px;font-size:12px;color:#ddd;line-height:1.5}
.foot-contact i{flex:none;width:22px;height:22px;border-radius:50%;background:#fff}
.email-box{margin-top:18px;width:216px;height:40px;border:1px solid #fff;border-radius:20px;position:relative;font-size:12px;color:#aaa;padding:11px 18px}
.email-box i{position:absolute;right:16px;top:13px;width:12px;height:12px;border-radius:50%;background:#fff}
.copyright{left:94px;top:4382px;color:#fff;font-size:12px}
.social-foot{left:966px;top:4375px;display:flex;gap:12px}
.social-foot i{width:24px;height:24px}
</style>
</head>
<body>

<!-- top bar -->
<div class="abs topbar">
  <div class="abs contact"><span>+1 (770) 555-0148</span><span>info@pinehollowhaven.org</span></div>
  <div class="abs donate">DONATE</div>
  <div class="abs social-top"><i></i><i></i><i></i><i></i></div>
</div>

<!-- navigation -->
<header class="abs navbar">
  <div class="abs brand"><span class="mark"></span><span class="name">Pine Hollow Haven Home Inc.</span></div>
  <nav class="abs nav" style="top:45px;left:0">
    <a class="active" style="left:300px">Home</a>
    <a style="left:381px">About</a>
    <a style="left:458px">How You Can Help</a>
    <a style="left:620px">Services Offered</a>
    <a style="left:768px">Our Love of Pets</a>
    <a style="left:917px">Contact Us</a>
    <a style="left:1030px">Haven Walk</a>
  </nav>
</header>

<!-- hero -->
<section class="abs hero" role="img" aria-label="Photo of a smiling young woman sitting outdoors with a laptop and a coffee cup"></section>
<svg class="abs" style="left:0;top:640px" width="1200" height="92" viewBox="0 0 1200 92" aria-hidden="true">
  <path d="M0 70 C300 92 600 40 900 30 C1030 26 1130 40 1200 60 L1200 92 L0 92Z" fill="#fff"/>
</svg>
<h1 class="abs hero-title">Haven Home</h1>
<div class="abs hero-sub">JOIN OUR TEAM!</div>
<div class="abs watch"><i></i>WATCH VIDEO</div>
<div class="abs hero-dots"><i></i><i class="on"></i><i></i><i></i></div>

<!-- about -->
<div class="abs about-bg" role="img" aria-label="Faint city street photo in the background"></div>
<h2 class="section-title" style="top:812px">WE ARE PINE HOLLOW HAVEN HOME</h2>
<p class="abs about-lead">With the help of our community, we have raised over 1000 girls and counting! Some of the services we offer include:</p>

<div class="abs center-photo"></div>
<div class="abs center-photo-fill" role="img" aria-label="Photo of a young woman sitting cross-legged with a laptop giving a thumbs up"></div>

<div class="feature left" style="left:74px;top:1025px">Room, Board, and<br>Watchful Oversight</div>
<div class="feat-icon" style="left:348px;top:1022px">
  <svg width="30" height="30" viewBox="0 0 30 30" fill="none" stroke="#333" stroke-width="1.6"><circle cx="15" cy="12" r="7"/><path d="M12 20h6M12 24h6"/></svg>
</div>
<div class="feature left" style="left:74px;top:1222px">Transitional<br>Living Services</div>
<div class="feat-icon" style="left:348px;top:1218px">
  <svg width="30" height="30" viewBox="0 0 30 30" fill="none" stroke="#333" stroke-width="1.6"><path d="M15 25 L5 15 A5 5 0 0 1 15 8 A5 5 0 0 1 25 15Z"/></svg>
</div>
<div class="feat-icon" style="left:822px;top:1016px">
  <svg width="30" height="30" viewBox="0 0 30 30" fill="none" stroke="#333" stroke-width="1.6"><rect x="7" y="6" width="16" height="18" rx="3"/><path d="M11 12h8M11 17h8"/></svg>
</div>
<div class="feature" style="left:908px;top:1020px">Independent<br>Living Services</div>
<div class="feat-icon" style="left:822px;top:1206px">
  <svg width="30" height="30" viewBox="0 0 30 30" fill="none" stroke="#333" stroke-width="1.6"><path d="M15 25 L5 15 A5 5 0 0 1 15 8 A5 5 0 0 1 25 15Z"/><path d="M10 15h10"/></svg>
</div>
<div class="feature" style="left:908px;top:1224px">Foster Gift Shop</div>

<!-- services -->
<section class="abs services-band">
  <h2 class="section-title">SERVICES OFFERED</h2>
</section>
<article class="card" style="left:119px;top:1700px">
  <div class="photo" role="img" aria-label="Photo of two young women studying together at a table" style="background:linear-gradient(135deg,#6d8f4f,#c9d2b3 60%,#e9e4d6)"><span class="play"></span></div>
  <h3>Life Skills Classes</h3>
  <p>The point of using Lorem Ipsum is that it has a more-or-less normal distribution</p>
  <span class="more">Read More »</span>
</article>
<article class="card highlight" style="left:452px;top:1700px">
  <div class="photo" role="img" aria-label="Photo of a young woman working on a laptop" style="background:linear-gradient(135deg,#7a4b32,#c68e64 55%,#efd7bd)"><span class="play"></span></div>
  <h3>Behavior Modification</h3>
  <p>The point of using Lorem Ipsum is that it has a more-or-less normal distribution</p>
  <span class="more">Read More »</span>
</article>
<article class="card" style="left:789px;top:1700px">
  <div class="photo" role="img" aria-label="Photo of three young women on a sofa looking at a laptop" style="background:linear-gradient(135deg,#b8b2a9,#e2ddd4 50%,#d9b04a)"><span class="play"></span></div>
  <h3>Resume Writing</h3>
  <p>The point of using Lorem Ipsum is that it has a more-or-less normal distribution</p>
  <span class="more">Read More »</span>
</article>
<div class="abs dots"><i class="on"></i><i></i><i></i></div>

<!-- testimonials -->
<h2 class="section-title" style="top:2245px">OUR TESTIMONIALS</h2>
<div class="testi" style="left:131px;top:2360px">
  <div class="avatar" role="img" aria-label="Portrait photo of a woman"></div>
  <div class="quote">“</div>
  <p>The point of using Lorem Ipsum is that it has a more-or-less normal distribution of letters, as opposed to using 'Content</p>
  <div class="stars">★★★★★</div>
  <div class="who">- &nbsp;Clara</div>
</div>
<div class="testi" style="left:652px;top:2360px">
  <div class="avatar" role="img" aria-label="Portrait photo of a woman"></div>
  <div class="quote">“</div>
  <p>The point of using Lorem Ipsum is that it has a more-or-less normal distribution of letters, as opposed to using 'Content</p>
  <div class="stars">★★★★★</div>
  <div class="who">- &nbsp;Rosa</div>
</div>

<!-- board members -->
<section class="abs board-band" role="img" aria-label="Dark blue band over a faint office photo">
  <h2 class="section-title">BOARD MEMBERS</h2>
</section>
<div class="arrow-btn" style="left:44px"><svg width="14" height="18" viewBox="0 0 14 18"><path d="M10 2 L3 9 L10 16" stroke="#fff" stroke-width="2.5" fill="none"/></svg></div>
<div class="arrow-btn" style="left:1110px"><svg width="14" height="18" viewBox="0 0 14 18"><path d="M4 2 L11 9 L4 16" stroke="#fff" stroke-width="2.5" fill="none"/></svg></div>
<div class="member" style="left:110px">
  <div class="avatar" role="img" aria-label="Portrait photo of a board member"></div>
  <h4>MARCUS HALE</h4><div class="role">Dolorem ipsum</div>
  <p>It is a long established fact that a reader will be distracted by the readable content of a page when looking</p>
</div>
<div class="member" style="left:447px">
  <div class="avatar" role="img" aria-label="Portrait photo of a board member"></div>
  <h4>NORA BELL</h4><div class="role">Neque quisquam</div>
  <p>It is a long established fact that a reader will be distracted by the readable content of a page when looking</p>
</div>
<div class="member" style="left:783px">
  <div class="avatar" role="img" aria-label="Portrait photo of a board member"></div>
  <h4>DANA REYES</h4><div class="role">Porro quisquam</div>
  <p>It is a long established fact that a reader will be distracted by the readable content of a page when looking</p>
</div>

<!-- latest events -->
<h2 class="section-title" style="top:3412px">LATEST EVENTS</h2>
<div class="abs calendar">
  <div class="cal-head"><b style="left:28px">‹</b><span class="mo">JUNE 2019</span><b style="right:28px">›</b></div>
  <table class="cal-grid">
    <tr><th>S</th><th>M</th><th>T</th><th>W</th><th>T</th><th>F</th><th>S</th></tr>
    <tr><td class="dim">28</td><td class="dim">29</td><td class="dim">30</td><td>1</td><td>2</td><td>3</td><td>4</td></tr>
    <tr><td>5</td><td>6</td><td>7</td><td>8</td><td>9</td><td>10</td><td>11</td></tr>
    <tr><td>12</td><td>13</td><td>14</td><td>15</td><td>16</td><td>17</td><td>18</td></tr>
    <tr><td>19</td><td>20</td><td>21</td><td>22</td><td class="today"><span>23</span></td><td>24</td><td>25</td></tr>
    <tr><td>26</td><td>27</td><td>28</td><td>29</td><td>30</td><td>31</td><td></td></tr>
  </table>
  <div class="cal-add">+</div>
</div>
<article class="event" style="left:441px">
  <div class="photo" role="img" aria-label="Photo of a young woman smiling at her laptop" style="background:linear-gradient(135deg,#8a6a58,#d3b9a6 55%,#eee8e2)"></div>
  <h4>Dolorem ipsum quia</h4>
  <p>The point of using Lorem Ipsum is that it has a more-or-less normal distribution</p>
  <div class="meta"><span class="stars">★★★★☆</span>15 Reviews</div>
  <span class="see">See All</span>
</article>
<article class="event" style="left:786px">
  <div class="photo" role="img" aria-label="Photo of three young women sharing a laptop on a sofa" style="background:linear-gradient(135deg,#8393ad,#d8d4cc 55%,#d6a94b)"></div>
  <h4>Neque porro quisquam</h4>
  <p>The point of using Lorem Ipsum is that it has a more-or-less normal distribution</p>
  <div class="meta"><span class="stars">★★★★☆</span>15 Reviews</div>
  <span class="see">See All</span>
</article>
<div class="abs view-more">View More »</div>

<!-- footer -->
<svg class="abs footer" viewBox="0 0 1200 427" preserveAspectRatio="none" aria-hidden="true">
  <path d="M0 30 C300 0 900 0 1200 30 L1200 427 L0 427Z" fill="#0e0e10"/>
  <path d="M0 30 C300 0 900 0 1200 30" fill="none" stroke="#9c1a3e" stroke-width="5"/>
</svg>
<div class="abs badge" role="img" aria-label="Anniversary badge placeholder"></div>
<div class="foot-col" style="left:342px">
  <h5>INFORMATION</h5>
  <ul><li>Privacy Policy</li><li>Your Account</li><li>Advanced Search</li><li>Contact Us</li></ul>
</div>
<div class="foot-col foot-contact" style="left:560px;width:220px">
  <h5>CONTACT US</h5>
  <div><i></i><span>418 Laurel Creek Rd, Ridgeview,<br>GA 30199, USA</span></div>
  <div><i></i><span>770.555.0192</span></div>
  <div><i></i><span>hello@pinehollowhaven.org</span></div>
</div>
<div class="foot-col" style="left:884px;width:240px">
  <h5>JOIN OUR MAILING LIST</h5>
  <div style="font-size:12px;line-height:1.6;color:#ddd">Your about us information would<br>fit here nicely.</div>
  <div class="email-box">Email address<i></i></div>
</div>
<div class="abs copyright">Copyright © 2019. All Rights Reserved</div>
<div class="abs social-foot"><i></i><i></i><i></i><i></i></div>

</body>
</html>
```